Business Card Design - Service Company

Use of the card mainly in living rooms and relations b2b We wish a card with a modern design, blue tones in the background would be a plus The card must be front / back (one side with the logo / the other with the information of contact )

Font styles to use
Serif

Requirements
Must have
• Using the map on the back of the business card Editable format! Photoshop CS2 / Illustrator CS2
Nice to have
• Mivrel Data IT Plein Ouest Commercial Center, 20417 Valmorre 0491847352 Siret 41873306200018 APE 9511Z https://www.fb.com/boutiquetech.mivreldata www.mivrel-data.com

```html
<!DOCTYPE html>
<html lang="en">
<head>
<meta charset="utf-8">
<title>Mivrel Data IT – Business Card</title>
<link href="https://fonts.googleapis.com/css2?family=Oswald:wght@500&family=Roboto:wght@400;500&display=swap" rel="stylesheet">
<style>
  :root {
    --page: #161617;
    --card: #1e1e1f;
    --card-light: #2c2c2d;
    --blue: #2a8ad4;
    --white: #f2f2f2;
  }
  * { box-sizing: border-box; margin: 0; padding: 0; }
  html, body { width: 1200px; height: 900px; overflow: hidden; }
  body {
    background: var(--page);
    font-family: "Roboto", Arial, sans-serif;
    color: var(--white);
    position: relative;
  }
  .card {
    position: absolute;
    left: 290px;
    width: 620px;
    height: 354px;
    background: linear-gradient(135deg, var(--card) 45%, var(--card-light) 100%);
    box-shadow: 0 10px 30px rgba(0,0,0,.6);
  }
  .card--front { top: 70px; }
  .card--back { top: 476px; }

  .brand {
    position: absolute;
    left: 0; right: 0; top: 140px;
    display: flex; align-items: center; justify-content: center; gap: 14px;
  }
  .brand__mark {
    width: 22px; height: 22px;
    background: var(--blue);
  }
  .brand__name {
    font-size: 42px; font-weight: 500; color: var(--blue);
    letter-spacing: 0.5px;
  }
  .registration {
    position: absolute; left: 0; right: 0; bottom: 36px;
    text-align: center; font-size: 15px; font-weight: 500; letter-spacing: .3px;
  }

  .person {
    position: absolute; left: 30px; top: 116px; width: 282px; text-align: right;
  }
  .person__name {
    font-family: "Oswald", "Arial Narrow", sans-serif;
    font-size: 42px; font-weight: 500; color: var(--blue);
    text-transform: uppercase; letter-spacing: 1px; line-height: 1.1;
  }
  .person__role { font-size: 17px; font-weight: 500; margin-top: 2px; }
  .divider {
    position: absolute; left: 332px; top: 126px;
    width: 2px; height: 76px; background: var(--blue);
  }
  .contacts {
    position: absolute; left: 356px; top: 128px;
    list-style: none; font-size: 17px; font-weight: 500; line-height: 24px;
  }
  .contacts li { display: flex; align-items: center; gap: 10px; }
  .contacts svg { width: 13px; height: 13px; flex: none; }
  .address {
    position: absolute; left: 0; right: 0; bottom: 40px;
    text-align: center; font-size: 18px; font-weight: 500;
  }
</style>
</head>
<body>
  <section class="card card--front">
    <div class="brand">
      <span class="brand__mark"></span>
      <span class="brand__name">Mivrel Data IT</span>
    </div>
    <p class="registration">Siret 41873306200018 APE 9511Z</p>
  </section>

  <section class="card card--back">
    <div class="person">
      <h1 class="person__name">Darel Quinton</h1>
      <p class="person__role">Director</p>
    </div>
    <span class="divider"></span>
    <ul class="contacts">
      <li>
        <svg viewBox="0 0 16 16" aria-hidden="true"><path fill="var(--blue)" d="M4 1l3 3-1.6 1.8a9 9 0 0 0 4.8 4.8L12 9l3 3-2 3C7 15 1 9 1 3z"/></svg>
        0491847352
      </li>
      <li>
        <svg viewBox="0 0 16 16" aria-hidden="true"><g fill="none" stroke="var(--blue)" stroke-width="1.4"><circle cx="8" cy="8" r="6.5"/><ellipse cx="8" cy="8" rx="3" ry="6.5"/><path d="M1.5 8h13"/></g></svg>
        www.mivrel-data.com
      </li>
      <li>
        <svg viewBox="0 0 16 16" aria-hidden="true"><circle cx="8" cy="8" r="5" fill="var(--blue)"/></svg>
        /boutiquetech.mivreldata
      </li>
    </ul>
    <p class="address">Plein Ouest Commercial Center, 20417 Valmorre</p>
  </section>
</body>
</html>
```